CalmPeak Nurses' Manifesto

Design a manifesto to inspire and motivate nurses to work at minimum standards of excellence in their nursing practice.

The manifesto will become a feature of our website, at conferences, workshops and retreats. It will also be featured on other marketing tools.

Primary Market:
Nurses and/or other healthcare professionals (specifically Doctors, Occupational Therapists, Psychologists and Social Workers).

However the manifesto is equally applicable to all nurses and healthcare professionals from new graduates to very experienced senior clinicians, administration officers,managers and healthcare executive personnel.

Mainly females and primarily 35 to 65 years old, which suggests people in this target age group have extensive experience, but have become jaded'.

The purpose of our business is to assist healthcare professionals, primarily nurses, to maintain their enthusiasm and excellence in service provision, for their benefit as well as the benefit of the clients.

I have attached:
File 1: Copy Samples and examples: which has the copy for the manifesto, examples that appeal to us and our 3 attempts.
File 2: Our colour Spec Sheet, HOWEVER the colours are not necessary limited to these colours. These colours are not in the logo that will be on the manifesto. The colours on the logo attached can/or also be used.
File 3: Prototype logo. The final logo will be available within 3 to 4 days.

Industry/Entity Type

Healthcare

Requirements
Must have
• Must use the copy as per the attached file.

It should be contemporary, eye catching and motivational.

Should not have
• MUST BE EASY TO READ. Each line MUST be clearly defined from each other.

```html
<!DOCTYPE html>
<html lang="en">
<head>
<meta charset="utf-8">
<title>CalmPeak Nurses' Manifesto</title>
<link href="https://fonts.googleapis.com/css2?family=Arimo:ital,wght@0,400;0,700;1,400;1,700&display=swap" rel="stylesheet">
<style>
  :root {
    --ink: #2c5a68;
    --leaf: #7cb342;
    --sea: #26a6a4;
    --char: #333b40;
    --star: #a9a9a9;
    --paper: #ffffff;
    --band: #1fa5a2;
    --rim: #9aa3a6;
  }
  * { margin: 0; padding: 0; box-sizing: border-box; }
  html, body { width: 922px; height: 1200px; overflow: hidden; background: var(--paper); }
  .manifesto {
    position: relative;
    width: 922px;
    height: 1200px;
    overflow: hidden;
    background: var(--paper);
    font-family: "Arimo", Arial, sans-serif;
  }
  .hero-photo {
    position: absolute;
    left: 330px;
    top: 0;
    width: 592px;
    height: 460px;
    background:
      linear-gradient(90deg, #ffffff 0%, rgba(255,255,255,0) 22%),
      linear-gradient(0deg, #ffffff 0%, rgba(255,255,255,0) 25%),
      linear-gradient(120deg, #6b3a2c 0%, #c98f78 30%, #e7c9ba 50%, #a9c4d6 70%, #dfe6ea 100%);
  }
  .brand {
    position: absolute;
    left: 120px;
    top: 70px;
    width: 240px;
    text-align: center;
  }
  .brand-dot {
    width: 110px;
    height: 110px;
    border-radius: 50%;
    background: var(--sea);
    margin: 0 auto 22px;
  }
  .brand-name {
    color: var(--ink);
    font-size: 34px;
    font-weight: 400;
    line-height: 1.05;
  }
  .title {
    position: absolute;
    left: 70px;
    top: 318px;
    font-size: 46px;
    font-weight: 700;
    font-style: italic;
    color: var(--ink);
  }
  .title .accent { color: var(--leaf); }
  .lines {
    position: absolute;
    left: 30px;
    top: 390px;
    width: 862px;
    font-weight: 700;
    font-style: italic;
    font-size: 19px;
    line-height: 25px;
    text-align: center;
    color: var(--char);
  }
  .lines .line { white-space: nowrap; }
  .lines .lead { font-size: 24px; line-height: 32px; text-align: left; padding-left: 120px; color: var(--ink); }
  .lines .gap { margin-top: 18px; }
  .star { color: var(--star); font-style: normal; font-size: 17px; padding: 0 4px; }
  .ink { color: var(--ink); }
  .leaf { color: var(--leaf); }
  .sea { color: var(--sea); }
  .char { color: var(--char); }
  .big { font-size: 23px; }
  .huge { font-size: 30px; }
  .underline { text-decoration: underline; }
  .closing {
    position: absolute;
    left: 110px;
    top: 950px;
    font-size: 34px;
    font-weight: 700;
    font-style: italic;
    color: var(--leaf);
  }
  .wave {
    position: absolute;
    left: 0;
    top: 880px;
    width: 922px;
    height: 320px;
  }
  .seal {
    position: absolute;
    left: 602px;
    top: 935px;
    width: 215px;
    height: 215px;
    border-radius: 50%;
    background: var(--paper);
    border: 4px solid var(--rim);
    display: flex;
    align-items: center;
    justify-content: center;
  }
  .seal-name {
    color: var(--ink);
    font-size: 32px;
    font-weight: 700;
    font-style: italic;
  }
</style>
</head>
<body>
<main class="manifesto">
  <div class="hero-photo" role="img" aria-label="Photograph of a smiling nurse with her arm around an elderly patient"></div>

  <div class="brand">
    <div class="brand-dot"></div>
    <div class="brand-name">Care Growth<br>Partners</div>
  </div>

  <h1 class="title">Nurses' <span class="accent">Manifesto</span></h1>

  <div class="lines">
    <div class="line lead"><span class="star">★</span>Nurse with open hands, hearts and minds.</div>
    <div class="line ink"><span class="star">★</span>Look after yourself and value your health as much as you value the</div>
    <div class="line"><span class="ink">health of others.</span> <span class="star">★</span><span class="leaf">Delight your clients and colleagues by exceeding</span></div>
    <div class="line"><span class="leaf">their expectations.</span> <span class="star">★</span><span class="sea big">Deliver care <span class="underline">skilfully</span>.</span> <span class="star">★</span><span class="ink">Respect the limits</span></div>
    <div class="line ink">of other people's knowledge and share your knowledge generously.</div>
    <div class="line"><span class="star">★</span><span class="leaf">Support your colleagues and champion their purpose.</span> <span class="star">★</span><span class="leaf">Learn</span></div>
    <div class="line"><span class="leaf">something new each day.</span> <span class="star">★</span><span class="ink">Trust your knowledge and seek</span></div>
    <div class="line"><span class="ink">advice only from respected sources.</span> <span class="star">★</span><span class="char">Be a lifelong learner.</span> <span class="star">★</span></div>
    <div class="line sea">Celebrate, respect and value the diversity of your culture. <span class="star">★</span></div>
    <div class="line"><span class="leaf">Respond to distress with random acts of kindness.</span> <span class="star">★</span><span class="ink">Smile and</span></div>
    <div class="line gap"><span class="ink">infect others with your happiness.</span> <span class="star">★</span><span class="sea huge">Have fun!</span> <span class="star">★</span><span class="leaf">Always</span></div>
    <div class="line"><span class="leaf">do the right thing without exception.</span> <span class="star">★</span><span class="sea">You are unique, revel in your</span></div>
    <div class="line"><span class="sea">individuality.</span> <span class="star">★</span><span class="leaf">Don't ever believe you've arrived, keep going.</span> <span class="star">★</span></div>
    <div class="line"><span class="char">Always be solution focused.</span> <span class="star">★</span><span class="ink">Seek success, firstly from within.</span> <span class="star">★</span></div>
    <div class="line"><span class="sea">Only follow exceptional leaders.</span> <span class="star">★</span><span class="ink">If there's no one left to follow, then</span></div>
    <div class="line"><span class="ink">lead!</span> <span class="star">★</span><span class="leaf">Always lead with purpose, passion and commitment.</span> <span class="star">★</span></div>
    <div class="line leaf">Respond to complex situations <span class="underline">innovatively</span>, creatively and safely</div>
    <div class="line"><span class="leaf">within the scope of your practice.</span> <span class="star">★</span><span class="sea">Adopt a 'can do' attitude to</span></div>
    <div class="line"><span class="sea">anything that comes your way.</span> <span class="star">★</span><span class="ink">Choose your thoughts wisely, they</span></div>
    <div class="line ink">create your reality.</div>
  </div>

  <p class="closing"><span class="star">★</span>Live your dream.</p>

  <svg class="wave" viewBox="0 0 922 320" aria-hidden="true">
    <path d="M0 215 C 250 270, 560 250, 700 180 C 790 135, 860 100, 922 90 L922 320 L0 320 Z" fill="#1fa5a2"/>
    <path d="M0 197 C 250 255, 560 232, 700 162 C 790 117, 860 82, 922 72" fill="none" stroke="#7cb342" stroke-width="5"/>
  </svg>

  <div class="seal">
    <span class="seal-name">CalmPeak</span>
  </div>
</main>
</body>
</html>
```